Electrician Letterhead Design MVR

We need some letterhead for our bills and other papers.
Customer address is on the right side (Swiss format)
A4 format

Design should also be applicable on Cards

Target Market(s)

Private Customers, Small Business

Industry/Entity Type

Electrician

Other font styles liked:
• incised 901

Colors
00AB8E
00BBA5
67D7C9
C6EFE9
E9F9F6

```html
<!DOCTYPE html>
<html lang="en">
<head>
<meta charset="utf-8">
<title>MVR Letterhead</title>
<link rel="stylesheet" href="https://fonts.googleapis.com/css2?family=Lato:wght@400;700;900&family=Parisienne&display=swap">
<style>
  :root {
    --teal: #009b87;
    --teal-light: #67c3b8;
    --ink: #222222;
    --paper: #ffffff;
    --backdrop: #e4e6e6;
  }
  * { box-sizing: border-box; margin: 0; padding: 0; }
  html, body {
    width: 1200px; height: 1200px; overflow: hidden;
    background: var(--backdrop);
    font-family: "Lato", sans-serif;
    color: var(--ink);
  }
  .letterhead {
    position: absolute; left: 204px; top: 40px;
    width: 792px; height: 1120px;
    background: var(--paper);
    box-shadow: 0 4px 18px rgba(0,0,0,0.12);
    overflow: hidden;
  }
  .header-wave { position: absolute; left: 0; top: 0; }
  .contact {
    position: absolute; left: 536px; top: 16px;
    color: #fff; font-size: 13px; line-height: 18px;
    list-style: none;
  }
  .contact .gap { margin-top: 5px; }
  .contact svg { width: 10px; height: 10px; margin-right: 6px; vertical-align: -1px; }
  .brand { position: absolute; left: 59px; top: 104px; }
  .brand-name {
    font-weight: 900; font-size: 74px; line-height: 74px;
    color: var(--teal); letter-spacing: -1px;
  }
  .brand-sub { font-size: 12px; font-weight: 700; margin-top: 2px; letter-spacing: 0.3px; }
  .letter {
    position: absolute; left: 60px; top: 244px; width: 672px;
    font-size: 15.5px;
  }
  .date { margin-bottom: 20px; }
  .recipient { line-height: 19px; margin-bottom: 17px; }
  .salutation { font-weight: 700; font-size: 17.5px; margin: 22px 0 18px; }
  .body p {
    font-size: 13.4px; line-height: 17.6px;
    text-align: justify; margin-bottom: 17px;
  }
  .closing { margin-top: 34px; font-size: 13.6px; }
  .signature {
    font-family: "Parisienne", cursive;
    font-size: 33px; margin-top: 18px; margin-left: 4px;
  }
  .footer-band { position: absolute; left: 0; bottom: 0; }
</style>
</head>
<body>
  <main class="letterhead">
    <svg class="header-wave" width="792" height="183" viewBox="0 0 563 130" aria-hidden="true">
      <path d="M0 0 H563 V128 C500 112 440 110 380 98 C300 80 200 38 100 38 C55 38 20 44 0 52 Z" fill="var(--teal)"/>
      <path d="M28 44 C60 20 110 6 170 8 C260 12 320 70 400 92 C460 104 520 100 563 96" fill="none" stroke="#fff" stroke-width="3.5"/>
    </svg>

    <ul class="contact">
      <li>42 Linden Road 7,</li>
      <li>Fairview, NY 10460</li>
      <li class="gap"><svg viewBox="0 0 10 10"><path d="M1 2 Q1 1 2 1 H3 L4 3 L3 4 Q4 6 6 7 L7 6 L9 7 V8 Q9 9 8 9 Q1 8 1 2Z" fill="#fff"/></svg>555-201-4830</li>
      <li><svg viewBox="0 0 10 10"><rect x="0.5" y="2" width="9" height="6.5" fill="#fff"/><path d="M0.5 2 L5 5.5 L9.5 2" fill="none" stroke="var(--teal)" stroke-width="0.8"/></svg>hello@mvrmail.com</li>
      <li><svg viewBox="0 0 10 10"><circle cx="5" cy="5" r="4.5" fill="#fff"/><path d="M0.5 5 H9.5 M5 0.5 V9.5 M5 0.5 Q2 5 5 9.5 M5 0.5 Q8 5 5 9.5" fill="none" stroke="var(--teal)" stroke-width="0.6"/></svg>www.mvrelectric.com</li>
    </ul>

    <div class="brand">
      <div class="brand-name">MVR</div>
      <div class="brand-sub">Elektrotechnik Mayer GmbH</div>
    </div>

    <article class="letter">
      <p class="date">Feb-03-2022</p>
      <p class="recipient">Mr, Paul Grant<br>President</p>
      <p class="recipient">Birch Corporation<br>123 Street Name, Suite# 10<br>City, State, 120023</p>
      <p class="salutation">Dear Mr, Paul</p>
      <div class="body">
        <p>Lorem ipsum dolor sit amet, consectetur adipisicing elit, sed do eiusmod tempor incididunt ut labore et dolore magna aliqua. Ut enim ad minim veniam, quis nostrud exercitation ullamco laboris nisi ut aliquip ex ea commodo consequat. Duis aute irure dolor in reprehenderit in voluptate velit esse cillum dolore eu fugiat nulla pariatur.</p>
        <p>Lorem ipsum dolor sit amet, consectetur adipisicing elit, sed do eiusmod tempor incididunt ut labore et dolore magna aliqua. Ut enim ad minim veniam, quis nostrud exercitation ullamco laboris nisi ut aliquip ex ea commodo consequat. Duis aute irure dolor in reprehenderit in voluptate velit esse cillum dolore eu fugiat nulla pariatur.</p>
        <p>Lorem ipsum dolor sit amet, consectetur adipisicing elit, sed do eiusmod tempor incididunt ut labore et dolore magna aliqua. Ut enim ad minim veniam, quis nostrud exercitation ullamco laboris nisi ut aliquip ex ea commodo consequat.</p>
        <p>Excepteur sint occaecat cupidatat non proident, sunt in culpa qui officia deserunt mollit anim id est laborum. re et dolore magnam aliquam quaerat voluptatem.</p>
      </div>
      <p class="closing">Regards</p>
      <p class="signature">Daniel Moore</p>
    </article>

    <svg class="footer-band" width="792" height="24" viewBox="0 0 792 24" aria-hidden="true">
      <polygon points="0,0 394,0 370,24 0,24" fill="var(--teal)"/>
      <polygon points="402,0 792,0 792,24 378,24" fill="var(--teal-light)"/>
    </svg>
  </main>
</body>
</html>
```